Need a small Brochure Designing for a High Tech LED Spotlight

This is an expensive product and the best of it's kind in the world, so it needs to be marketed to intelligent, forward thinking people who appreciate and pay for excellent design and innovation. The type of people who buy Quince products i guess. It needs to be clean. The colours do not need to be in keep with our website, but our logo does need to be on the brochure. I have attached a dcoument with all the text, the order the text goes in and an idea of how i want the first page to look. All images and logos have been attached too.

Target Market(s)

This is aimed at people with high disposible incomes who spend money on the best designed products and the latest technology. The type of people who buy Quince products.

Industry/Entity Type

Product

Requirements
Must have
• The work needs to be editable by us using indesign

The pages need to be A5. I'm not sure how many pages the brochure needs to be as it does need to be clean and be spaced out well. On the file that contains the text i've indicated that 8 pages would be good.

The logos i attached - 1) Brava Product Design Award, 2) K Technology Award, 3) Tall Oak Design Award and 4) Keen Form Award all need to be at the bottom of the front page, quite small, but still able to see them well.

- Needs to have a QR code so that smart phones can scan the code and be taken to a zen pier clip - QR code is attached.
- Needs to have Tumbolt Icon - @BrightNookCo
Nice to have
• Nice to remind customers on each page that the product has a 5 year Warranty and we have a 365 day Returns Policy.

```html
<!DOCTYPE html>
<html lang="en">
<head>
<meta charset="utf-8">
<title>N4 7w Brochure Cover</title>
<link rel="stylesheet" href="https://fonts.googleapis.com/css2?family=Quicksand:wght@300;500;700&display=swap">
<style>
  :root {
    --canvas: #ffffff;
    --page: #ffffff;
    --page-edge: #dcdcdc;
    --fold: #9a9a9a;
    --headline: #6f6f6f;
    --accent-green: #2f8f3a;
    --logo-ink: #1a1a1a;
    --badge-fill: #d9d9d9;
    --photo-light: #f6efe6;
    --photo-mid: #cdb99b;
    --photo-deep: #8c7556;
  }
  * { margin: 0; padding: 0; box-sizing: border-box; }
  html, body {
    width: 1200px; height: 900px; overflow: hidden;
    background: var(--canvas);
    font-family: "Quicksand", sans-serif;
  }
  .canvas { position: relative; width: 1200px; height: 900px; }
  .cover-page {
    position: absolute; left: 0; top: 85px; width: 1152px; height: 712px;
    background: var(--page);
    border: 1px solid var(--page-edge); border-left: none;
    box-shadow: 0 2px 6px rgba(0,0,0,0.12);
  }
  .fold-line {
    position: absolute; left: 115px; top: 0; bottom: 0;
    border-left: 1px dotted var(--fold);
  }
  .product-photo {
    position: absolute; left: 185px; top: 160px; width: 510px; height: 545px;
    background: radial-gradient(ellipse 46% 44% at 60% 40%, var(--photo-light) 0%, var(--photo-light) 22%, var(--photo-mid) 40%, var(--photo-deep) 58%, var(--photo-mid) 66%, rgba(255,255,255,0) 74%);
  }
  .product-model {
    position: absolute; left: 731px; top: 307px;
    font-size: 25px; font-weight: 700; color: var(--accent-green);
    letter-spacing: 0.5px; line-height: 1;
  }
  .headline {
    position: absolute; left: 727px; top: 338px;
    font-size: 70px; font-weight: 300; line-height: 64px;
    color: var(--headline); white-space: nowrap;
  }
  .award-strip { position: absolute; left: 193px; top: 610px; width: 155px; height: 74px; }
  .brand-logo {
    position: absolute; left: 730px; top: 630px;
    display: flex; align-items: center; gap: 10px;
  }
  .brand-text { display: flex; flex-direction: column; align-items: center; color: var(--logo-ink); }
  .brand-name { font-size: 22px; font-weight: 700; line-height: 1; }
  .brand-tagline { font-size: 9px; font-weight: 700; margin-top: 3px; }
  .brand-mark { width: 22px; height: 22px; border-radius: 50%; background: var(--accent-green); }
</style>
</head>
<body>
<div class="canvas">
  <section class="cover-page">
    <div class="fold-line"></div>
    <div class="product-photo" role="img" aria-label="Gold-finned LED spotlight with glowing lens and soft reflection below"></div>
    <p class="product-model">N4 7w</p>
    <h1 class="headline">Simple<br>Beautiful<br>Intelligent</h1>
    <svg class="award-strip" viewBox="0 0 155 74" role="img" aria-label="Design award badges">
      <rect x="0" y="4" width="34" height="34" fill="var(--badge-fill)"/>
      <rect x="40" y="4" width="34" height="34" fill="var(--badge-fill)"/>
      <rect x="80" y="4" width="34" height="34" fill="var(--badge-fill)"/>
      <rect x="120" y="4" width="34" height="34" fill="var(--badge-fill)"/>
    </svg>
    <div class="brand-logo">
      <div class="brand-text">
        <span class="brand-name">Bright Nook</span>
        <span class="brand-tagline">Specialists in quality</span>
      </div>
      <span class="brand-mark"></span>
    </div>
  </section>
</div>
</body>
</html>
```